Aunt Roula's Bakery

I am about to create a luxury boutique that specializes in cake baking and cupcake
and ready for parties and special events and order delivery
the logo has already made

Boutique

Email:auntroulasbakery@mailbox-example.net
Instagram: aunt_roula_bakery
Twitter: xxxxxxx
WhatsApp: xxxxxxx

Requirements
Must have
• luxury design

```html
<!DOCTYPE html>
<html lang="en">
<head>
<meta charset="utf-8">
<title>Aunt Roula's Bakery – Business Card</title>
<link rel="stylesheet" href="https://fonts.googleapis.com/css2?family=Source+Sans+3:wght@400;600&display=swap">
<style>
  :root {
    --page-bg: #e9e4df;
    --card-bg: #f4f2f0;
    --card-edge: #d6d1cd;
    --rose: #b45b72;
    --rose-deep: #9c4660;
    --rose-light: #c97b8e;
    --wave-line: #55504f;
    --brand-ink: #8e4a5b;
    --on-rose: #ffffff;
    --on-rose-soft: #f6e6ea;
  }
  * { box-sizing: border-box; margin: 0; padding: 0; }
  html, body {
    width: 1200px;
    height: 969px;
    overflow: hidden;
    background: var(--page-bg);
    font-family: "Source Sans 3", "Myriad Pro", Arial, sans-serif;
  }
  .business-card {
    position: absolute;
    left: 100px;
    top: 201px;
    width: 1000px;
    height: 567px;
    border-radius: 26px;
    background: var(--card-bg);
    border: 1px solid var(--card-edge);
    overflow: hidden;
    box-shadow: 0 18px 40px rgba(60, 40, 40, 0.12);
  }
  .card-wave {
    position: absolute;
    inset: 0;
    width: 100%;
    height: 100%;
  }
  .brand-name {
    position: absolute;
    left: 24px;
    top: 176px;
    width: 400px;
    text-align: center;
    font-weight: 600;
    font-size: 40px;
    line-height: 1.2;
    color: var(--brand-ink);
    white-space: nowrap;
  }
  .person {
    position: absolute;
    right: 58px;
    top: 222px;
    text-align: right;
    color: var(--on-rose);
  }
  .person-name {
    font-weight: 600;
    font-size: 34px;
    line-height: 1.1;
  }
  .person-role {
    font-weight: 400;
    font-size: 25px;
    margin-top: 4px;
    color: var(--on-rose-soft);
  }
  .contact-list {
    position: absolute;
    right: 58px;
    top: 327px;
    list-style: none;
  }
  .contact-item {
    display: flex;
    align-items: center;
    justify-content: flex-end;
    height: 37.5px;
    font-size: 22px;
    color: var(--on-rose-soft);
  }
  .contact-icon {
    width: 26px;
    height: 26px;
    margin-left: 26px;
    flex: none;
  }
  .contact-dot {
    width: 20px;
    height: 20px;
    margin: 0 3px 0 29px;
    border-radius: 50%;
    background: var(--on-rose-soft);
    flex: none;
  }
</style>
</head>
<body>
  <main class="business-card">
    <svg class="card-wave" viewBox="0 0 550 312" preserveAspectRatio="none" aria-hidden="true">
      <defs>
        <linearGradient id="roseBand" x1="0" y1="0" x2="1" y2="1">
          <stop offset="0" stop-color="var(--rose-light)"/>
          <stop offset="0.5" stop-color="var(--rose)"/>
          <stop offset="1" stop-color="var(--rose-deep)"/>
        </linearGradient>
      </defs>
      <path d="M0 232 C 60 280, 150 292, 230 225 C 300 160, 360 90, 440 70 C 490 58, 520 60, 550 62 L550 312 L0 312 Z" fill="url(#roseBand)"/>
      <path d="M0 226 C 60 274, 150 286, 230 219 C 300 154, 360 80, 440 62 C 490 50, 520 52, 550 54" fill="none" stroke="var(--wave-line)" stroke-width="2.2"/>
    </svg>

    <p class="brand-name">Aunt Roula's Bakery</p>

    <div class="person">
      <h1 class="person-name">Daniel Mercer</h1>
      <p class="person-role">CEO/Founder</p>
    </div>

    <ul class="contact-list">
      <li class="contact-item">
        <span>555 214 0187</span>
        <svg class="contact-icon" viewBox="0 0 24 24" aria-label="Phone">
          <path d="M6.6 10.8a15.1 15.1 0 0 0 6.6 6.6l2.2-2.2c.3-.3.7-.4 1-.2 1.1.4 2.3.6 3.6.6.6 0 1 .4 1 1V20c0 .6-.4 1-1 1A17 17 0 0 1 3 4c0-.6.4-1 1-1h3.5c.6 0 1 .4 1 1 0 1.3.2 2.5.6 3.6.1.3 0 .7-.2 1z" fill="var(--on-rose-soft)"/>
        </svg>
      </li>
      <li class="contact-item">
        <span>auntroulasbakery@mailbox-example.net</span>
        <svg class="contact-icon" viewBox="0 0 24 24" aria-label="Email">
          <rect x="2" y="5" width="20" height="14" rx="1.5" fill="var(--on-rose-soft)"/>
          <path d="M3 6.5l9 6.5 9-6.5" fill="none" stroke="var(--rose)" stroke-width="1.6"/>
        </svg>
      </li>
      <li class="contact-item">
        <span>aunt_roula_bakery</span>
        <span class="contact-dot"></span>
      </li>
      <li class="contact-item">
        <span>auntroulasbakery</span>
        <span class="contact-dot"></span>
      </li>
      <li class="contact-item">
        <span>auntroulasbakery</span>
        <span class="contact-dot"></span>
      </li>
    </ul>
  </main>
</body>
</html>
```